Quillmont Energy b-card redesign

I would like to redesign the card (and power point template) for quillmont energy. We are a developer/owner/operator of high-tech biomass gasification power plants. We take ag waste like nut shells or fruit pits and convert that into electricity in the 1/2 - 3 MW range. I would like to change our company color from red to golden gate bridge orange (C=0,M=69,,Y=100,B=6).

```html
<!DOCTYPE html>
<html lang="en">
<head>
<meta charset="utf-8">
<title>Quillmont Energy – Business Card</title>
<link rel="stylesheet" href="https://fonts.googleapis.com/css2?family=Marcellus&family=Michroma&display=swap">
<style>
  :root {
    --stage: #e7e6e3;
    --card-white: #ffffff;
    --card-shade: #e9e9ea;
    --panel-dark: #232224;
    --accent-orange: #f04a00;
    --ink: #2a2a2c;
    --ink-light: #ffffff;
  }
  * { margin: 0; padding: 0; box-sizing: border-box; }
  html, body {
    width: 1200px; height: 899px; overflow: hidden;
    background: var(--stage);
  }
  .card {
    position: absolute; left: 100px; top: 164px;
    width: 1000px; height: 571px; overflow: hidden;
    background: radial-gradient(ellipse at 45% 45%, var(--card-white) 0%, #f6f6f6 55%, var(--card-shade) 100%);
    box-shadow: 0 18px 40px rgba(0,0,0,0.18);
  }
  .card__panel { position: absolute; inset: 0; width: 1000px; height: 571px; }
  .brand {
    position: absolute; left: 110px; top: 150px;
    font-family: "Marcellus", serif; font-size: 46px;
    letter-spacing: 2px; color: var(--ink); white-space: nowrap;
  }
  .person {
    position: absolute; right: 26px; top: 252px; text-align: right;
    font-family: "Michroma", sans-serif; color: var(--ink-light);
    white-space: nowrap;
  }
  .person__name { font-size: 18px; letter-spacing: 1px; }
  .person__role { font-size: 12px; letter-spacing: 1.5px; margin-top: 8px; }
  .contact {
    position: absolute; left: 110px; top: 330px;
    font-family: "Michroma", sans-serif; color: var(--ink); font-size: 15px;
  }
  .contact__address { line-height: 26px; margin-bottom: 20px; }
  .contact__row { display: flex; align-items: center; gap: 12px; height: 30px; }
  .contact__icon { width: 18px; height: 18px; fill: var(--ink); flex: none; }
</style>
</head>
<body>
  <div class="card">
    <svg class="card__panel" viewBox="0 0 1000 571" aria-hidden="true">
      <path d="M812 0 C716 120 700 430 770 571 L1000 571 L1000 0 Z" fill="var(--panel-dark)"/>
      <path d="M806 0 C710 120 694 430 764 571" fill="none" stroke="var(--accent-orange)" stroke-width="5"/>
    </svg>

    <div class="brand">QUILLMONT ENERGY</div>

    <div class="person">
      <div class="person__name">DANIEL ROYCE</div>
      <div class="person__role">FINANCIAL ADVISOR</div>
    </div>

    <div class="contact">
      <div class="contact__address">062.14th floor,Crest<br>Harbor Road LKG</div>
      <div class="contact__row">
        <svg class="contact__icon" viewBox="0 0 24 24"><path d="M6.6 10.8a15 15 0 0 0 6.6 6.6l2.2-2.2a1 1 0 0 1 1-.25 11.4 11.4 0 0 0 3.6.57 1 1 0 0 1 1 1V20a1 1 0 0 1-1 1A17 17 0 0 1 3 4a1 1 0 0 1 1-1h3.5a1 1 0 0 1 1 1c0 1.25.2 2.45.57 3.57a1 1 0 0 1-.25 1z"/></svg>
        <span>012 345 6789</span>
      </div>
      <div class="contact__row">
        <svg class="contact__icon" viewBox="0 0 24 24"><path d="M7 1h10a2 2 0 0 1 2 2v18a2 2 0 0 1-2 2H7a2 2 0 0 1-2-2V3a2 2 0 0 1 2-2zm0 3v14h10V4zm5 15.5a1.2 1.2 0 1 0 0 2.4 1.2 1.2 0 0 0 0-2.4z"/></svg>
        <span>012 345 6789</span>
      </div>
      <div class="contact__row">
        <svg class="contact__icon" viewBox="0 0 24 24"><path d="M8 2h9v6H8zM4 8h3v14H4zm4 2h13v12H8zm3 3v2h2v-2zm4 0v2h2v-2zm-4 4v2h2v-2zm4 0v2h2v-2z"/></svg>
        <span>012 345 6789</span>
      </div>
      <div class="contact__row">
        <svg class="contact__icon" viewBox="0 0 24 24"><path d="M2 5h20v14H2zm2 2v.5l8 5.5 8-5.5V7zm0 3v7h16v-7l-8 5.5z"/></svg>
        <span>urname@email.com</span>
      </div>
      <div class="contact__row">
        <svg class="contact__icon" viewBox="0 0 24 24"><path d="M12 2a10 10 0 1 0 0 20 10 10 0 0 0 0-20zm6.9 6h-3a15 15 0 0 0-1.3-3.9A8 8 0 0 1 18.9 8zM12 4c.8 1.2 1.4 2.5 1.8 4h-3.6c.4-1.5 1-2.8 1.8-4zM4.3 14a8 8 0 0 1 0-4h3.4a16 16 0 0 0 0 4zm.8 2h3a15 15 0 0 0 1.3 3.9A8 8 0 0 1 5.1 16zm3-8h-3a8 8 0 0 1 4.3-3.9A15 15 0 0 0 8.1 8zM12 20c-.8-1.2-1.4-2.5-1.8-4h3.6c-.4 1.5-1 2.8-1.8 4zm2.3-6H9.7a14 14 0 0 1 0-4h4.6a14 14 0 0 1 0 4zm.3 5.9a15 15 0 0 0 1.3-3.9h3a8 8 0 0 1-4.3 3.9zm1.7-5.9a16 16 0 0 0 0-4h3.4a8 8 0 0 1 0 4z"/></svg>
        <span>www.urwebsitename.com</span>
      </div>
    </div>
  </div>
</body>
</html>
```